Lawn care business card

I am looking for a quality designed personal business card to represent the quality and elegant nature of our company. We separate ourselves in our market by the aesthetic value of our work, so I am looking for marketing material that does the same. We target our marketing high end customers, and we try to avoid price shoppers. I am open to all design options, so long as they are in line with our companies values.

We are tend to go with a retro look on everything from our logo and print material, to our uniforms. We like to portray and "old fashion" set of core values, with a modern elegance. So a wild and crazy look is out of the question.

Things I'd like on the card:
1.) Logo
2.) Phone number: (816) 555-2931
3.) Website: Verdelynkc.com
4.) Email: robertfairley@verdelynkc.com
5.) My name: Robert Fairley
6.) Facebook link: facebook.com/VerdelynGardenandGrounds
7.) Instagram: http://instagram.com/verdelynkc

Attached is a copy of our logo.

Reason: More time is needed to gather conclusive feedback from the members of our marketing team.

```html
<!DOCTYPE html>
<html lang="en">
<head>
<meta charset="utf-8">
<title>Verdelyn Garden and Grounds – Business Card</title>
<link rel="stylesheet" href="https://fonts.googleapis.com/css2?family=Arimo:wght@400;700&display=swap">
<style>
  :root {
    --backdrop: #e4e4e2;
    --card-white: #f7f7f5;
    --card-black: #1e1f1f;
    --orange: #dc5a22;
    --text-light: #f2f2f2;
    --text-dark: #1e1f1f;
  }
  * { margin: 0; padding: 0; box-sizing: border-box; }
  html, body {
    width: 1200px;
    height: 1000px;
    overflow: hidden;
    background: var(--backdrop);
    font-family: "Arimo", Arial, sans-serif;
  }
  .canvas {
    position: relative;
    width: 1200px;
    height: 1000px;
  }
  .card {
    position: absolute;
    left: 220px;
    width: 760px;
    height: 434px;
    overflow: hidden;
    box-shadow: 0 4px 14px rgba(0,0,0,0.18);
  }
  .card-front {
    top: 38px;
    background: var(--card-white);
    display: flex;
    align-items: center;
    justify-content: center;
    gap: 22px;
  }
  .brand-dot {
    width: 34px;
    height: 34px;
    border-radius: 50%;
    background: var(--orange);
  }
  .brand-name {
    font-weight: 700;
    font-size: 66px;
    letter-spacing: 3px;
    color: var(--text-dark);
  }
  .card-back {
    top: 528px;
    background: var(--card-black);
    color: var(--text-light);
  }
  .accent-band {
    position: absolute;
    top: 0;
    bottom: 0;
    background: var(--orange);
  }
  .accent-band--wide { right: 0; width: 22px; }
  .accent-band--thin { right: 34px; width: 5px; }
  .contact-top {
    position: absolute;
    left: 50px;
    top: 46px;
  }
  .holder-name {
    font-weight: 700;
    font-size: 25px;
    margin-bottom: 8px;
  }
  .contact-line {
    font-size: 16px;
    line-height: 1.55;
    white-space: nowrap;
  }
  .contact-bottom {
    position: absolute;
    left: 250px;
    top: 318px;
  }
  .contact-bottom .contact-line {
    font-size: 17px;
    line-height: 1.55;
  }
</style>
</head>
<body>
<main class="canvas">
  <section class="card card-front" aria-label="Card front">
    <span class="brand-dot"></span>
    <span class="brand-name">Verdelyn</span>
  </section>

  <section class="card card-back" aria-label="Card back">
    <span class="accent-band accent-band--thin"></span>
    <span class="accent-band accent-band--wide"></span>

    <div class="contact-top">
      <p class="holder-name">Robert Fairley</p>
      <p class="contact-line">Phone : (816) 555-2931</p>
      <p class="contact-line">Email: robertfairley@verdelynkc.com</p>
    </div>

    <div class="contact-bottom">
      <p class="contact-line">Website : Verdelynkc.com</p>
      <p class="contact-line">Instagram : http://instagram.com/verdelynkc</p>
      <p class="contact-line">Facebook : facebook.com/VerdelynGardenandGrounds</p>
    </div>
  </section>
</main>
</body>
</html>
```